3rd Annual Tamsin Valley Fun Day Fundraiser

This is our 3rd Annual Tamsin Valley Fun Day Dog Wash Extravagana to support Helpers of Tamsin Valley Pet Center. Please see the attached flyer for the 2nd Annual. We loved this flyer! Please revamp with our logo attached and the new content provided. Let's keep to the same colors as the 2nd Annual flyer-no change. Date: Saturday April 25th 2020 10A-1PM. Rain Date: May 2nd. Same address as 2nd Annual.

Other font styles liked:
• See 2nd Annual Flyer

Colors
add136
e34297
6b449b

Requirements
Must have
• See attached 2nd annual flyer including colors
Nice to have

```html
<!DOCTYPE html>
<html lang="en">
<head>
<meta charset="utf-8">
<title>Tamsin Valley Fun Day Fundraiser Flyer</title>
<link href="https://fonts.googleapis.com/css2?family=Montserrat:wght@700;800&family=Roboto:ital,wght@0,400;0,500;1,400&display=swap" rel="stylesheet">
<style>
  :root {
    --green: #add136;
    --pink: #e34297;
    --purple: #6b449b;
    --ink: #3d3d3d;
    --page: #d9d9d9;
    --paper: #ffffff;
    --paper-fade: #eceeed;
  }
  * { box-sizing: border-box; margin: 0; padding: 0; }
  html, body { width: 1062px; height: 1200px; overflow: hidden; }
  body { background: var(--page); font-family: "Roboto", Arial, sans-serif; color: var(--ink); }

  .flyer {
    position: absolute; left: 105px; top: 0; width: 852px; height: 1200px;
    background: linear-gradient(180deg, var(--paper) 55%, var(--paper-fade) 85%);
    overflow: hidden;
  }
  .hero-photo {
    position: absolute; left: 0; top: 0; width: 852px; height: 620px;
    background: linear-gradient(180deg, #8fbce6 0%, #b9d3e0 18%, #6f9a55 34%, #8a7f74 55%, #c9c2b8 75%, #b7b1a8 100%);
  }
  .hero-wave { position: absolute; left: 0; top: 400px; width: 852px; height: 220px; }

  .event-name {
    position: absolute; left: 470px; top: 420px; width: 360px;
    font-family: "Montserrat", Arial, sans-serif; font-weight: 800; font-size: 30px;
    line-height: 1.1; color: var(--paper); text-align: center;
  }

  .headline { position: absolute; left: 64px; top: 0; font-family: "Montserrat", Arial, sans-serif; font-weight: 800; line-height: 1; }
  .headline span { position: absolute; left: 0; white-space: nowrap; }
  .headline .line-one { top: 545px; color: var(--purple); font-size: 66px; }
  .headline .line-two { top: 622px; color: var(--pink); font-size: 48px; }

  .when { position: absolute; left: 66px; top: 700px; font-size: 20px; }
  .when .row { position: absolute; left: 0; white-space: nowrap; display: flex; align-items: baseline; }
  .when .label { font-family: "Montserrat", Arial, sans-serif; font-weight: 700; color: var(--purple); font-size: 24px; width: 92px; }
  .when .row-date { top: 0; }
  .when .row-rain { top: 34px; }
  .when .row-time { top: 72px; }

  .where { position: absolute; left: 489px; top: 712px; width: 320px; font-size: 19px; line-height: 25px; }

  .donate-link, .donate-button {
    position: absolute; top: 817px; height: 33px; border-radius: 17px; color: #fff;
    font-size: 18px; line-height: 33px; white-space: nowrap;
  }
  .donate-link { left: 46px; width: 570px; background: var(--pink); padding-left: 20px; }
  .donate-link strong { font-weight: 500; }
  .donate-button {
    left: 622px; width: 184px; background: var(--purple); text-align: center;
    font-family: "Montserrat", Arial, sans-serif; font-weight: 700; font-size: 17px;
  }

  .contact-mark {
    position: absolute; width: 130px; height: 60px; display: flex; align-items: center; justify-content: center;
    font-size: 14px; line-height: 1.2; text-align: center; color: var(--purple); font-weight: 500;
  }
  .contact-mark.left { left: 30px; top: 918px; }
  .contact-mark.right { left: 450px; top: 910px; }
  .contact-card { position: absolute; top: 888px; }
  .contact-card.left { left: 173px; }
  .contact-card.right { left: 580px; }
  .contact-name { font-family: "Montserrat", Arial, sans-serif; font-weight: 700; color: var(--pink); font-size: 19px; margin-bottom: 6px; white-space: nowrap; }
  .contact-info { font-size: 15px; line-height: 23px; white-space: nowrap; }

  .perks { position: absolute; left: 0; top: 1004px; width: 852px; height: 120px; background: var(--green); }
  .perks ul { position: absolute; top: 16px; list-style: none; }
  .perks ul.first { left: 72px; }
  .perks ul.second { left: 470px; }
  .perks li { color: #fff; font-size: 19px; line-height: 29px; display: flex; align-items: center; gap: 10px; white-space: nowrap; }
  .perks svg { width: 17px; height: 17px; flex: none; }

  .footer-note {
    position: absolute; left: 0; top: 1124px; width: 852px; height: 76px; background: var(--purple);
    color: #fff; font-style: italic; font-size: 18px; line-height: 26px; text-align: center; padding-top: 12px;
  }
</style>
</head>
<body>
<svg width="0" height="0" style="position:absolute">
  <symbol id="paw" viewBox="0 0 20 20">
    <ellipse cx="10" cy="13.5" rx="5" ry="4.2" fill="#e34297"/>
    <circle cx="3.5" cy="8" r="2.2" fill="#e34297"/>
    <circle cx="7.5" cy="4" r="2.2" fill="#e34297"/>
    <circle cx="12.5" cy="4" r="2.2" fill="#e34297"/>
    <circle cx="16.5" cy="8" r="2.2" fill="#e34297"/>
  </symbol>
</svg>

<main class="flyer">
  <div class="hero-photo" role="img" aria-label="Group photo of smiling teen volunteers outdoors with a mascot costume, trees and blue sky behind"></div>
  <svg class="hero-wave" viewBox="0 0 852 220" preserveAspectRatio="none" aria-hidden="true">
    <path d="M0 20 C180 -6 430 40 852 194 L852 220 L0 220 Z" fill="#add136"/>
    <path d="M0 34 C180 10 430 58 852 206 L852 220 L0 220 Z" fill="#ffffff"/>
  </svg>

  <div class="event-name">Tamsin Valley Fun Day</div>

  <h1 class="headline">
    <span class="line-one">A FAMILY</span>
    <span class="line-two">FUN EVENT FOR ALL AGES</span>
  </h1>

  <section class="when">
    <div class="row row-date"><span class="label">Date:</span><span>Saturday April 25th 2020</span></div>
    <div class="row row-rain"><span class="label"></span><span>Rain Date: May 2nd</span></div>
    <div class="row row-time"><span class="label">Time:</span><span>10A - 1PM</span></div>
  </section>
  <address class="where" style="font-style:normal">Harborline Realty, 418 Fernwood<br>Ave. Alder Springs FL 32990<br>Alder Springs Town Center</address>

  <div class="donate-link"><strong>To Make a Donation:</strong> https://www.tamsinvalleypets.org/give</div>
  <div class="donate-button">CLICK: DONATE</div>

  <div class="contact-mark left">Harborline Realty</div>
  <div class="contact-card left">
    <div class="contact-name">DANA WHITCOMBE</div>
    <div class="contact-info">Harborline Realty Corp.<br>555.201.4478<br>dana@harborlinerealty.com</div>
  </div>
  <div class="contact-mark right">Helpers of Tamsin Valley Pet Center</div>
  <div class="contact-card right">
    <div class="contact-name">MEGAN CASTELL</div>
    <div class="contact-info">HTVPC<br>555.318.9026<br>megan-castell@mailbay.net</div>
  </div>

  <section class="perks">
    <ul class="first">
      <li><svg><use href="#paw"/></svg>FREE Doggie Wash</li>
      <li><svg><use href="#paw"/></svg>Food &amp; Beverages</li>
      <li><svg><use href="#paw"/></svg>Vendors (FREE give-a-Ways)</li>
    </ul>
    <ul class="second">
      <li><svg><use href="#paw"/></svg>Raffle Drawings | Grand Prize</li>
      <li><svg><use href="#paw"/></svg>Donations Welcome</li>
      <li><svg><use href="#paw"/></svg>Adoptions by HTVPC</li>
    </ul>
  </section>

  <footer class="footer-note">All domestic breeds from puppies to seniors invited.<br>Please be sure Furry Fido is tolerant of other dogs, crowds and bathing</footer>
</main>
</body>
</html>
```